Website for Excavator and Earthworks Company

We require a modern, sleek and practical website for our newly created earthworks/excavator business in Perth, Western Australia called Bluegum Ridge Earthworks.

The website should have a modern, cutting edge feel but only needs to be relatively simplistic in it's layout and eventual functionality.

Some pages it should have would be Home, About, Projects and Contact Us.

```html
<!DOCTYPE html>
<html lang="en">
<head>
<meta charset="utf-8">
<title>Bluegum Ridge Earthworks</title>
<link href="https://fonts.googleapis.com/css2?family=Montserrat:wght@600;700;800&family=Lato:wght@400;700&display=swap" rel="stylesheet">
<style>
:root{
  --lime:#b6d11b;
  --lime-dark:#8fa612;
  --ink:#111111;
  --text:#333333;
  --muted:#555555;
  --white:#ffffff;
  --line:#e3e3e3;
}
*{box-sizing:border-box;margin:0;padding:0}
html,body{width:1200px;height:4728px;overflow:hidden}
body{position:relative;background:var(--white);font-family:'Lato',sans-serif;color:var(--text)}
.abs{position:absolute}
h1,h2,h3,.brand,.nav,.btn{font-family:'Montserrat',sans-serif}
.btn{display:inline-block;background:var(--lime);color:var(--ink);font-weight:600;font-size:15px;padding:9px 22px;border-radius:4px;text-decoration:none}
.placeholder{position:absolute;overflow:hidden}

/* header */
.site-header{position:absolute;top:0;left:0;width:1200px;height:96px;z-index:5;display:flex;align-items:center;padding:0 112px}
.brand{display:flex;align-items:center;gap:10px;color:var(--white);font-weight:800;font-size:22px;letter-spacing:.5px}
.brand-mark{width:26px;height:26px;background:var(--lime)}
.nav{margin-left:auto;display:flex;align-items:center;gap:34px;font-size:15px;font-weight:600;color:var(--white)}
.nav a{color:var(--white);text-decoration:none}
.nav .active{background:var(--lime);color:var(--ink);padding:7px 14px;border-radius:4px}
.nav .btn{margin-left:30px}

/* hero */
.hero-photo{top:0;left:0;width:1200px;height:820px;background:linear-gradient(100deg,rgba(10,14,20,.85) 0%,rgba(20,28,40,.55) 45%,rgba(0,0,0,0) 70%),linear-gradient(180deg,#4d6584 0%,#8ea3b6 35%,#b89a6e 70%,#6a4d33 100%)}
.hero-copy{top:240px;left:112px;width:560px;color:var(--white)}
.hero-copy h1{font-size:44px;line-height:1.15;font-weight:800;letter-spacing:.5px}
.hero-copy h1 span{color:var(--lime)}
.hero-copy p{font-size:19px;line-height:1.5;margin:30px 0 36px;width:460px}

.features{top:600px;left:0;width:1200px;height:320px}
.feature{position:absolute;border-radius:50%;display:flex;flex-direction:column;align-items:center;justify-content:center;text-align:center;padding:0 40px}
.feature h3{font-size:19px;font-weight:800;line-height:1.2;margin:14px 0 10px}
.feature p{font-size:12.5px;line-height:1.45}
.feature.dark{background:var(--ink);color:var(--white);width:290px;height:290px;top:20px}
.feature.lime{background:var(--lime);color:var(--white);width:300px;height:300px;top:10px;left:458px;border:6px solid var(--ink)}
.feature.dark h3{color:var(--white)}
.feature .icon{width:54px;height:54px}

/* sections */
.section-title{font-size:38px;font-weight:800;color:var(--ink);letter-spacing:.5px}
.center{text-align:center}
.rule{width:60px;height:3px;background:var(--lime);margin:8px 0 0}
.body-copy{font-size:16px;line-height:1.55;color:var(--muted)}

.about-photo{top:1020px;left:112px;width:430px;height:408px;border-radius:14px;background:linear-gradient(150deg,#9fb3c6 0%,#c88a46 45%,#6d5a48 100%)}
.about-copy{top:1050px;left:620px;width:470px}
.about-copy .body-copy{margin-top:30px}
.about-copy .body-copy+.body-copy{margin-top:22px}
.about-copy .btn{margin-top:30px}

.mission-head{top:1540px;left:0;width:1200px}
.mission-head p{width:760px;margin:24px auto 0;font-size:16px;line-height:1.55;color:var(--muted)}
.mission-card{top:1704px;width:306px;height:296px;background:var(--white);border:1px solid var(--line);border-radius:8px;box-shadow:0 6px 16px rgba(0,0,0,.12);padding:28px}
.mission-card.featured{border:2px solid var(--lime)}
.mission-card h3{font-size:20px;font-weight:800;color:var(--ink);margin:18px 0 12px}
.mission-card p{font-size:14px;line-height:1.55;color:var(--muted)}
.icon-disc{width:60px;height:60px;border-radius:50%;background:var(--ink);display:flex;align-items:center;justify-content:center}
.mission-card.featured .icon-disc{background:var(--lime)}

/* services */
.services-bg{top:2080px;left:0;width:1200px;height:840px}
.services-head{top:2190px;left:0;width:1200px;color:var(--white)}
.services-head .section-title{color:var(--white)}
.services-head p{width:760px;margin:14px auto 0;font-size:15px;line-height:1.5}
.service-card{top:2346px;width:304px;height:346px;background:var(--white);border-radius:8px;overflow:hidden;box-shadow:0 6px 16px rgba(0,0,0,.2)}
.service-card .thumb{height:176px;margin:8px;border-radius:6px}
.service-card .info{padding:10px 18px}
.service-card h3{font-size:20px;font-weight:800;color:var(--ink)}
.service-card p{font-size:14px;line-height:1.5;color:var(--muted);margin:10px 0 14px}
.service-card .btn{font-size:13px;padding:7px 16px}
.arrow{width:34px;height:34px;border-radius:50%;background:var(--ink);top:2500px;display:flex;align-items:center;justify-content:center}

/* team */
.team-copy{top:2950px;left:112px;width:500px}
.team-copy .section-title{margin-top:20px}
.team-copy .body-copy{margin-top:26px}
.team-copy .body-copy+.body-copy{margin-top:22px}
.team-copy .btn{margin-top:30px}
.team-photo{top:2952px;left:652px;width:436px;height:400px;border-radius:14px;background:linear-gradient(160deg,#a9bccc 0%,#c9a24b 50%,#5b5f4b 100%)}

/* projects */
.projects-head{top:3470px;left:0;width:1200px}
.projects-head p{width:720px;margin:22px auto 0;font-size:16px;line-height:1.55;color:var(--muted)}
.tile{border-radius:6px}
.view-all{top:4160px;left:545px}

/* footer */
.site-footer{top:4280px;left:0;width:1200px;height:448px;background:var(--ink);color:var(--white)}
.footer-brand{position:absolute;top:120px;left:0;width:1200px;display:flex;justify-content:center}
.footer-brand .brand{font-size:38px}
.footer-brand .brand-mark{width:44px;height:44px}
.footer-nav{position:absolute;top:248px;left:0;width:1200px;display:flex;justify-content:center;gap:0;font-family:'Lato',sans-serif;font-size:15px}
.footer-nav a{color:var(--white);text-decoration:none;padding:0 38px;border-right:1px solid #666}
.footer-nav a:last-child{border-right:none}
.socials{position:absolute;top:310px;left:0;width:1200px;display:flex;justify-content:center;gap:18px}
.socials span{width:28px;height:28px;border-radius:50%;background:var(--white)}
.socials span:first-child{background:var(--lime)}
.copyright{position:absolute;top:410px;left:0;width:1200px;text-align:center;font-size:13px;color:#ccc}
</style>
</head>
<body>

<!-- Hero -->
<div class="placeholder hero-photo" role="img" aria-label="Excavator digging at an earthworks site at sunset"></div>

<header class="site-header">
  <div class="brand"><span class="brand-mark"></span>BLUEGUM RIDGE EARTHWORKS</div>
  <nav class="nav">
    <a class="active" href="#">Home</a>
    <a href="#">About Us</a>
    <a href="#">Projects</a>
    <a href="#">Contact Us</a>
    <a class="btn" href="#">Get Started</a>
  </nav>
</header>

<div class="abs hero-copy">
  <h1>RAISING THE STANDARD<br><span>IN EARTHWORKS</span></h1>
  <p>High-quality excavation and earthmoving services delivered with precision across Perth and WA.</p>
  <a class="btn" href="#">Request a Quote</a>
</div>

<svg class="abs" style="top:640px;left:0" width="1200" height="340" viewBox="0 0 1200 340">
  <path d="M0 150 L200 110 L200 190 L0 230 Z" fill="#b6d11b"/>
  <path d="M1000 110 L1200 60 L1200 150 L1000 190 Z" fill="#b6d11b"/>
  <path d="M0 200 Q600 150 1200 130 L1200 340 L0 340 Z" fill="#ffffff"/>
</svg>

<div class="abs features">
  <div class="feature dark" style="left:200px">
    <svg class="icon" viewBox="0 0 54 54"><circle cx="27" cy="27" r="18" fill="none" stroke="#b6d11b" stroke-width="4"/><circle cx="27" cy="27" r="7" fill="#b6d11b"/></svg>
    <h3>LOCAL<br>WA EXPERTISE</h3>
    <p>Risus commodo viverra maecenas accumsan lacus vel facilisis.</p>
  </div>
  <div class="feature lime">
    <svg class="icon" viewBox="0 0 54 54"><circle cx="27" cy="27" r="24" fill="#111"/><circle cx="27" cy="27" r="14" fill="none" stroke="#b6d11b" stroke-width="3"/><circle cx="27" cy="27" r="5" fill="#b6d11b"/></svg>
    <h3>PRECISION-FOCUSED<br>WORK</h3>
    <p>Risus commodo viverra maecenas accumsan lacus vel facilisis.</p>
  </div>
  <div class="feature dark" style="left:724px">
    <svg class="icon" viewBox="0 0 54 54"><circle cx="27" cy="27" r="22" fill="#b6d11b"/><path d="M27 15 V27 L35 33" stroke="#111" stroke-width="4" fill="none" stroke-linecap="round"/></svg>
    <h3>RELIABLE &amp; ON<br>TIME</h3>
    <p>Risus commodo viverra maecenas accumsan lacus vel facilisis.</p>
  </div>
</div>

<!-- About -->
<div class="placeholder about-photo" role="img" aria-label="Two site workers in hi-vis gear reviewing plans"></div>
<div class="abs about-copy">
  <h2 class="section-title">ABOUT US</h2>
  <div class="rule"></div>
  <p class="body-copy">Lorem ipsum dolor sit amet, consectetur adipiscing elit, sed do eiusmod tempor incididunt ut labore et dolore magna aliqua. Ut enim ad minim veniam, quis nostrud exercitation ullamco laboris nisi ut aliquip ex ea commodo consequat.</p>
  <p class="body-copy">Sed ut perspiciatis unde omnis iste natus error sit voluptatem accusantium doloremque laudantium, totam rem aperiam, eaque ipsa quae ab illo inventore veritatis et quasi architecto beatae vitae dicta sunt explicabo.</p>
  <a class="btn" href="#">Read More</a>
</div>

<!-- Mission -->
<div class="abs mission-head center">
  <h2 class="section-title">OUR MISSION</h2>
  <div class="rule" style="margin:8px auto 0"></div>
  <p>Bluegum Ridge Earthworks delivers professional excavation and earthmoving services tailored to residential, commercial, and site preparation projects.</p>
</div>
<div class="abs mission-card" style="left:112px">
  <div class="icon-disc"><svg width="30" height="30" viewBox="0 0 30 30"><circle cx="15" cy="15" r="11" fill="none" stroke="#b6d11b" stroke-width="3"/><circle cx="15" cy="15" r="4" fill="#b6d11b"/></svg></div>
  <h3>DELIVER PRECISION</h3>
  <p>Lorem ipsum dolor sit amet, consectetur adipiscing elit, sed do eiusmod et tempor incididunt ut labore et dolore magna aliqua.</p>
</div>
<div class="abs mission-card featured" style="left:448px">
  <div class="icon-disc"><svg width="30" height="30" viewBox="0 0 30 30"><circle cx="15" cy="15" r="10" fill="none" stroke="#111" stroke-width="4" stroke-dasharray="5 3"/><circle cx="15" cy="15" r="4" fill="#111"/></svg></div>
  <h3>OPERATE RELIABLY</h3>
  <p>Lorem ipsum dolor sit amet, consectetur adipiscing elit, sed do eiusmod et tempor incididunt ut labore et dolore magna aliqua.</p>
</div>
<div class="abs mission-card" style="left:784px">
  <div class="icon-disc"><svg width="30" height="30" viewBox="0 0 30 30"><path d="M5 16 L12 23 L25 8" fill="none" stroke="#b6d11b" stroke-width="4" stroke-linecap="round" stroke-linejoin="round"/></svg></div>
  <h3>LOCAL COMMITMENT</h3>
  <p>Lorem ipsum dolor sit amet, consectetur adipiscing elit, sed do eiusmod et tempor incididunt ut labore et dolore magna aliqua.</p>
</div>

<!-- Services -->
<div class="placeholder services-bg" role="img" aria-label="Excavator working on site under a lime green overlay" style="background:linear-gradient(180deg,#a9c21a 0%,#9cb81c 50%,#7f9816 100%)"></div>
<svg class="abs" style="top:2010px;left:0" width="1200" height="200" viewBox="0 0 1200 200">
  <path d="M0 30 L1200 100 L1200 160 L0 160 Z" fill="#b6d11b"/>
  <path d="M0 20 L560 110 L0 150 Z" fill="#111"/>
  <path d="M1200 60 L780 110 L1200 150 Z" fill="#111"/>
</svg>
<div class="abs services-head center">
  <h2 class="section-title">OUR SERVICES</h2>
  <p>We provide reliable excavation and earthworks services across Perth and Western Australia, delivering clean, accurate results for residential and commercial projects.</p>
</div>
<div class="abs arrow" style="left:52px"><svg width="14" height="14" viewBox="0 0 14 14"><path d="M9 2 L4 7 L9 12" fill="none" stroke="#fff" stroke-width="2.5"/></svg></div>
<div class="abs arrow" style="left:1114px"><svg width="14" height="14" viewBox="0 0 14 14"><path d="M5 2 L10 7 L5 12" fill="none" stroke="#fff" stroke-width="2.5"/></svg></div>

<div class="abs service-card" style="left:116px">
  <div class="placeholder thumb" style="position:relative;background:linear-gradient(160deg,#8fa5ba,#d1a53a 60%,#6b5b45)" role="img" aria-label="Excavator on an earthworks site"></div>
  <div class="info"><h3>EARTHWORKS</h3><p>Lorem ipsum dolor sit amet, consectetur adipiscing elit, sed do eiusmod tempor incididunt ut magna aliqua.</p><a class="btn" href="#">Read More</a></div>
</div>
<div class="abs service-card" style="left:450px">
  <div class="placeholder thumb" style="position:relative;background:linear-gradient(160deg,#a7b7c4,#d9a93c 55%,#806447)" role="img" aria-label="Excavator digging ground"></div>
  <div class="info"><h3>EXCAVATION</h3><p>Lorem ipsum dolor sit amet, consectetur adipiscing elit, sed do eiusmod tempor incididunt ut magna aliqua.</p><a class="btn" href="#">Read More</a></div>
</div>
<div class="abs service-card" style="left:784px">
  <div class="placeholder thumb" style="position:relative;background:linear-gradient(160deg,#c9b79a,#b98a4f 55%,#5e4632)" role="img" aria-label="Excavator bucket cutting a trench"></div>
  <div class="info"><h3>TRENCHING</h3><p>Lorem ipsum dolor sit amet, consectetur adipiscing elit, sed do eiusmod tempor incididunt ut magna aliqua.</p><a class="btn" href="#">Read More</a></div>
</div>

<svg class="abs" style="top:2790px;left:0" width="1200" height="140" viewBox="0 0 1200 140">
  <path d="M0 130 L1200 10 L1200 140 L0 140 Z" fill="#ffffff"/>
  <path d="M900 40 L1200 10 L1200 22 L900 52 Z" fill="#111"/>
</svg>

<!-- Team -->
<div class="abs team-copy">
  <h2 class="section-title" style="margin-top:110px">OUR TEAM</h2>
  <div class="rule"></div>
  <p class="body-copy">Lorem ipsum dolor sit amet, consectetur adipiscing elit, sed do eiusmod tempor incididunt ut labore et dolore magna aliqua. Ut enim ad minim veniam, quis nostrud exercitation ullamco laboris nisi ut aliquip ex ea commodo consequat.</p>
  <p class="body-copy">Sed ut perspiciatis unde omnis iste natus error sit voluptatem accusantium doloremque laudantium, totam rem aperiam, eaque ipsa quae ab illo inventore veritatis et quasi architecto beatae vitae dicta sunt explicabo.</p>
  <a class="btn" href="#">Meet the Team</a>
</div>
<div class="placeholder team-photo" role="img" aria-label="Three crew members in hard hats and hi-vis vests on site"></div>

<!-- Projects -->
<div class="abs projects-head center">
  <h2 class="section-title">OUR PROJECTS</h2>
  <div class="rule" style="margin:8px auto 0"></div>
  <p>Bluegum Ridge Earthworks delivers professional excavation and earthworks services tailored to residential, commercial, and site preparation projects.</p>
</div>
<div class="placeholder tile" style="top:3628px;left:112px;width:230px;height:244px;background:linear-gradient(160deg,#8ea7be,#d2a348 60%,#7a5a3c)" role="img" aria-label="Excavator at work on a site"></div>
<div class="placeholder tile" style="top:3628px;left:356px;width:396px;height:244px;background:linear-gradient(160deg,#b6c0c6,#d2a139 50%,#8a6a43)" role="img" aria-label="Bulldozer pushing soil"></div>
<div class="placeholder tile" style="top:3628px;left:766px;width:322px;height:244px;background:linear-gradient(160deg,#a6a58e,#7f6f55 50%,#5b4b38)" role="img" aria-label="Worker in hard hat beside machinery"></div>
<div class="placeholder tile" style="top:3884px;left:112px;width:318px;height:244px;background:linear-gradient(160deg,#8a8d86,#c05a2a 50%,#4f4a42)" role="img" aria-label="Worker in orange overalls on a rail corridor"></div>
<div class="placeholder tile" style="top:3884px;left:444px;width:396px;height:244px;background:linear-gradient(160deg,#b3c1cb,#c6a04c 50%,#6d6250)" role="img" aria-label="Site workers with excavators in the background"></div>
<div class="placeholder tile" style="top:3884px;left:856px;width:232px;height:244px;background:linear-gradient(160deg,#c9c3b7,#d77a2c 50%,#6b5a48)" role="img" aria-label="Compact excavator on a worksite"></div>
<a class="abs btn view-all" href="#">View All</a>

<!-- Footer -->
<footer class="abs site-footer">
  <svg class="abs" style="top:-60px;left:0" width="1200" height="120" viewBox="0 0 1200 120">
    <path d="M0 60 L1200 0 L1200 120 L0 120 Z" fill="#111"/>
    <path d="M760 40 L1200 12 L1200 24 L760 52 Z" fill="#b6d11b"/>
    <path d="M0 90 L420 70 L420 78 L0 98 Z" fill="#b6d11b"/>
  </svg>
  <div class="footer-brand"><div class="brand"><span class="brand-mark"></span>BLUEGUM RIDGE EARTHWORKS</div></div>
  <nav class="footer-nav">
    <a href="#">Home</a><a href="#">About Us</a><a href="#">Services</a><a href="#">Contact Us</a><a href="#">Terms &amp; conditions</a><a href="#">Privacy policy</a>
  </nav>
  <div class="socials"><span></span><span></span><span></span></div>
  <p class="copyright">Copyright © 2024 Bluegum Ridge Earthworks. All rights reserved.</p>
</footer>

</body>
</html>
```